We need a complete design for our construction company KELTO CONSTRUCTION based in Auckland New Zealand, we need a logo, website, business card, vehicle design etc..
We are a mid to high-end construction company who work mostly on residential projects and some commercial.

What we want to see in the design;
Professional,
Architectural,
Simple,
Alternative,

We want the design to communicate professionalism, high quality wormanship and and quality service.

Target Market(s)

People looking for a quality building/ construction company

Industry/Entity Type

Construction Company

Contact Information for Business Card

KELTO CONSTRUCTION.co.nz
Lino Verasek
lino@keltoconstruction.example.nz
021 5807 462

Logo Text

KELTO CONSTRUCTION

Number of Pages Required

5+ page

Font styles to use
Sans Serif

Colors

Designer to choose colors to be used in the design.

Requirements
Must have
• Must appear high end, professional, quality, be simple, easy to use, give security to potential clients
Nice to have
• high-quality photos of our recent projects
• about us page
• blog page
• contact us page
• high quality content
Should not have
• should not be hard to use and have too much going on.

```html
<!DOCTYPE html>
<html lang="en">
<head>
<meta charset="utf-8">
<title>Kelto Constructions</title>
<link href="https://fonts.googleapis.com/css2?family=Open+Sans:wght@300;400;600;700&family=Ubuntu:wght@400;500;700&display=swap" rel="stylesheet">
<style>
:root{
  --teal:#6fc8bd;
  --teal-dark:#5bb5aa;
  --ink:#3a3a3a;
  --muted:#6d6d6d;
  --line:#d6d6d6;
  --paper:#ffffff;
  --mist:#efefef;
  --night:#2e2e2e;
  --photo-sky:#8fa2b4;
  --photo-warm:#b7a07a;
}
*{margin:0;padding:0;box-sizing:border-box}
html,body{width:1200px;height:3564px;overflow:hidden}
body{position:relative;background:var(--paper);font-family:"Open Sans",sans-serif;color:var(--ink)}
section,header,nav,footer{position:absolute;left:0;width:1200px}
.abs{position:absolute}
.heading{font-family:"Ubuntu",sans-serif;font-weight:500;color:var(--teal);font-size:37px;text-align:center;width:1200px;left:0;letter-spacing:.5px}
.btn{position:absolute;background:var(--teal);color:#fff;font-family:"Ubuntu",sans-serif;font-weight:500;font-size:19px;display:flex;align-items:center;justify-content:center;letter-spacing:.3px}
.photo{position:absolute}

/* header */
.site-header{top:0;height:145px;background:var(--paper)}
.brand{left:78px;top:30px;height:82px;display:flex;align-items:center;gap:16px}
.brand-square{width:14px;height:14px;background:var(--teal)}
.brand-name{font-family:"Open Sans",sans-serif;font-weight:400;color:var(--teal);font-size:28px;letter-spacing:5px}
.contact-chip{top:50px;display:flex;gap:16px;align-items:flex-start}
.chip-box{width:50px;height:50px;border:1.5px solid #bdbdbd;display:flex;align-items:center;justify-content:center}
.chip-text{font-size:15px;line-height:23px;color:var(--muted);padding-top:2px}
.chip-text .accent{color:var(--teal)}

/* nav */
.main-nav{top:145px;height:53px;background:var(--night)}
.main-nav a{position:absolute;top:0;line-height:53px;color:#fff;font-size:16px;text-decoration:none;font-family:"Open Sans",sans-serif}
.main-nav a.current{color:var(--teal)}

/* hero */
.hero{top:198px;height:564px;background:linear-gradient(120deg,#7d8a94 0%,#a9b4bd 35%,#c8ced3 55%,#8895a0 100%)}
.hero-frame{left:340px;top:127px;width:520px;height:312px;border:10px solid rgba(255,255,255,.45)}
.hero-title{top:228px;width:1200px;text-align:center;color:#fff;font-family:"Ubuntu",sans-serif;font-weight:500;font-size:50px;letter-spacing:.5px}
.hero-sub{top:297px;width:1200px;text-align:center;color:#fff;font-weight:700;font-size:22px}

/* about */
.about{top:762px;height:458px}
.about .heading{top:50px}
.about-text{left:236px;top:108px;width:728px;text-align:center;font-size:15px;line-height:25px;color:var(--muted)}
.value{top:228px;width:362px;text-align:center}
.value svg{display:block;margin:0 auto}
.value p{margin-top:22px;font-size:19px;color:#8a8a8a}
.divider{top:228px;width:1px;height:145px;background:var(--line)}

/* projects */
.projects{top:1220px;height:948px;background:var(--mist)}
.projects .heading{top:52px}
.project-accent{left:78px;top:137px;width:520px;height:393px;background:var(--teal)}
.project-detail{left:722px;top:250px;width:400px}
.project-name{font-size:29px;color:var(--ink)}
.designer{display:flex;align-items:center;gap:20px;margin-top:18px}
.avatar{width:60px;height:60px;border-radius:50%;background:linear-gradient(135deg,#d9b48c,#8f6a4a)}
.designer-name{font-size:17px;line-height:26px;color:var(--ink)}
.designer-role{font-size:15px;color:var(--muted)}
.project-text{margin-top:20px;font-size:16px;line-height:27px;color:var(--muted);width:392px}
.dots{top:883px;left:568px;display:flex;gap:6px}
.dots span{width:15px;height:15px;border-radius:50%;border:1.5px solid var(--teal)}
.dots span.on{background:var(--teal)}

/* blog */
.blog{top:2168px;height:635px}
.blog .heading{top:52px}
.post{top:112px;width:324px}
.post .photo{position:relative;height:217px;width:324px}
.post-meta{display:flex;justify-content:space-between;margin-top:26px;font-size:15px;color:var(--muted)}
.post-meta span{display:flex;align-items:center;gap:10px}
.post-title{margin-top:16px;font-family:"Ubuntu",sans-serif;font-size:19px;line-height:30px;color:var(--ink)}
.post-text{margin-top:8px;font-size:15px;line-height:24px;color:var(--muted)}
.read-more{margin-top:14px;font-family:"Ubuntu",sans-serif;font-weight:500;font-size:15px;color:var(--teal);text-decoration:underline;display:flex;align-items:center;gap:10px}

/* contact */
.contact{top:2803px;height:635px;background:var(--mist)}
.contact .heading{top:52px}
.info-card{top:125px;width:324px;height:170px;border:1.5px solid var(--line);display:flex;flex-direction:column;align-items:center;justify-content:center;gap:18px;text-align:center;font-size:15px;line-height:24px;color:var(--ink)}
.field{height:40px;border-bottom:1.5px solid var(--line);font-size:15px;color:#8a8a8a;padding-left:22px;line-height:30px}

/* footer */
.site-footer{top:3438px;height:126px;background:var(--night);color:#fff}
.footer-links{top:34px;width:1200px;text-align:center;font-size:15px}
.footer-links a{color:#fff;text-decoration:none;margin:0 22px}
.copyright{top:82px;width:1200px;text-align:center;font-size:15px}
</style>
</head>
<body>

<header class="site-header">
  <div class="abs brand">
    <span class="brand-square"></span>
    <span class="brand-name">KELTO CONSTRUCTION</span>
  </div>
  <div class="abs contact-chip" style="left:650px">
    <div class="chip-box">
      <svg width="20" height="24" viewBox="0 0 20 24"><path d="M10 1a8 8 0 0 0-8 8c0 6 8 14 8 14s8-8 8-14a8 8 0 0 0-8-8z" fill="var(--teal)"/><circle cx="10" cy="9" r="3" fill="#fff"/></svg>
    </div>
    <div class="chip-text">123, building, street, city,<br>country, zipcode.</div>
  </div>
  <div class="abs contact-chip" style="left:955px">
    <div class="chip-box">
      <svg width="22" height="22" viewBox="0 0 24 24"><path d="M6.6 10.8a15 15 0 0 0 6.6 6.6l2.2-2.2c.3-.3.7-.4 1-.2 1.1.4 2.3.6 3.6.6.6 0 1 .4 1 1V20c0 .6-.4 1-1 1A17 17 0 0 1 3 4c0-.6.4-1 1-1h3.5c.6 0 1 .4 1 1 0 1.3.2 2.5.6 3.6.1.3 0 .7-.2 1z" fill="var(--teal)"/></svg>
    </div>
    <div class="chip-text">123 456 7890<br><span class="accent">Call Us Now</span></div>
  </div>
</header>

<nav class="main-nav">
  <a class="current" style="left:132px" href="#">HOME</a>
  <a style="left:283px" href="#">ABOUT</a>
  <a style="left:431px" href="#">PROJECTS</a>
  <a style="left:600px" href="#">BLOG</a>
  <a style="left:737px" href="#">CONTACT US</a>
</nav>

<section class="hero">
  <div class="photo" role="img" aria-label="Photo of two builders in hard hats and hi-vis vests reviewing plans on site" style="inset:0;background:linear-gradient(115deg,rgba(120,110,70,.55) 0%,rgba(150,160,170,.3) 40%,rgba(200,205,210,.2) 60%,rgba(90,100,115,.5) 100%)"></div>
  <div class="abs hero-frame"></div>
  <div class="abs hero-title">KELTO CONSTRUCTIONS</div>
  <div class="abs hero-sub">Designed For Lifestyle, Built to Last.</div>
  <div class="btn" style="left:507px;top:389px;width:186px;height:50px">CONTACT US</div>
</section>

<section class="about">
  <h2 class="abs heading">ABOUT KELTO CONSTRUCTIONS</h2>
  <p class="abs about-text">Lorem Ipsum is simply dummy text of the printing and typesetting industry. Lorem Ipsum has been the industry's standard dummy text ever since the 1500s, when an unknown printer took a galley of type and scrambled it to make a type specimen book. It has survived not only five centuries.</p>

  <div class="abs value" style="left:58px">
    <svg width="84" height="76" viewBox="0 0 84 76" fill="none" stroke="var(--teal)" stroke-width="4">
      <path d="M30 6c-14 0-24 8-24 19 0 6 3 11 8 14l-4 10 12-6c3 1 5 1 8 1 14 0 24-8 24-19S44 6 30 6z"/>
      <path d="M54 30c12 1 22 8 22 18 0 5-3 9-7 12l3 9-11-5c-2 1-5 1-7 1-10 0-18-5-21-12" fill="var(--teal)" stroke="none"/>
      <circle cx="46" cy="49" r="2.6" fill="#fff" stroke="none"/><circle cx="55" cy="49" r="2.6" fill="#fff" stroke="none"/><circle cx="64" cy="49" r="2.6" fill="#fff" stroke="none"/>
    </svg>
    <p>Communicate professionalism</p>
  </div>
  <div class="abs divider" style="left:420px"></div>
  <div class="abs value" style="left:420px">
    <svg width="76" height="76" viewBox="0 0 76 76" fill="none" stroke="var(--teal)" stroke-width="4.5">
      <circle cx="38" cy="38" r="34"/><path d="M22 38l11 11 22-22" stroke-linecap="round" stroke-linejoin="round"/>
    </svg>
    <p>High quality wormanship</p>
  </div>
  <div class="abs divider" style="left:782px"></div>
  <div class="abs value" style="left:782px">
    <svg width="70" height="84" viewBox="0 0 70 84" fill="none" stroke="var(--teal)" stroke-width="3.5">
      <circle cx="35" cy="32" r="28"/><circle cx="35" cy="32" r="19"/>
      <path d="M35 22l3 7 7 .5-5.5 4.5 2 7-6.5-4-6.5 4 2-7-5.5-4.5 7-.5z" stroke-linejoin="round"/>
      <path d="M22 56l-6 24 9-4 6 7 4-21M48 56l6 24-9-4-6 7-4-21" stroke-linejoin="round"/>
    </svg>
    <p>And quality service.</p>
  </div>
</section>

<section class="projects">
  <h2 class="abs heading">LATEST PROJECT</h2>
  <div class="abs project-accent"></div>
  <div class="photo" role="img" aria-label="Photo of a modern commercial building entrance at sunset" style="left:120px;top:177px;width:520px;height:396px;background:linear-gradient(160deg,#3a3f4a 0%,#6c6a78 30%,#c48b6a 48%,#9aa0a8 62%,#7c7f84 100%)"></div>
  <div class="abs project-detail">
    <div class="project-name">Project Name</div>
    <div class="designer">
      <div class="avatar" role="img" aria-label="Designer portrait photo"></div>
      <div>
        <div class="designer-name">Designer Name</div>
        <div class="designer-role">Info</div>
      </div>
    </div>
    <p class="project-text">Lorem Ipsum is simply dummy text of the printing and typesetting industry. Lorem Ipsum has been the industry's standard dummy text ever since the.</p>
  </div>
  <div class="btn" style="left:720px;top:475px;width:167px;height:41px;font-size:17px">GET LOCATION</div>

  <div class="photo" role="img" aria-label="Photo of a brick retail building" style="left:78px;top:637px;width:323px;height:208px;background:linear-gradient(180deg,#3d6bb0 0%,#6a90c8 45%,#a47c62 65%,#7d7468 100%)"></div>
  <div class="photo" role="img" aria-label="Photo of engineers in hard hats on a construction site" style="left:438px;top:637px;width:323px;height:208px;background:linear-gradient(180deg,#cfd8de 0%,#b9c2c6 40%,#c9c24a 65%,#7a7466 100%)"></div>
  <div class="photo" role="img" aria-label="Photo of a glass office tower seen from below" style="left:798px;top:637px;width:324px;height:208px;background:linear-gradient(135deg,#1d3f7a 0%,#4c78b8 45%,#a9c4e2 75%,#e8eef5 100%)"></div>

  <div class="abs dots"><span class="on"></span><span></span><span></span></div>
</section>

<section class="blog">
  <h2 class="abs heading">LATEST BLOG</h2>

  <article class="abs post" style="left:78px">
    <div class="photo" role="img" aria-label="Photo of a builder in a yellow hard hat reading on a tablet" style="background:linear-gradient(135deg,#b36a3a 0%,#8a7b62 40%,#c8b03a 65%,#5a5a4e 100%)"></div>
    <div class="post-meta">
      <span><svg width="16" height="16" viewBox="0 0 16 16"><rect x="1" y="3" width="14" height="12" fill="none" stroke="var(--teal)" stroke-width="1.8"/><rect x="1" y="3" width="14" height="4" fill="var(--teal)"/><path d="M4 1v3M12 1v3" stroke="var(--teal)" stroke-width="1.8"/></svg>05 May 2017</span>
      <span><svg width="16" height="16" viewBox="0 0 16 16"><path d="M2 14l1-4 8-8 3 3-8 8z" fill="var(--teal)"/></svg>By Admin</span>
    </div>
    <h3 class="post-title">Lorem Ipsum is simply dummy text of the printing.</h3>
    <p class="post-text">Lorem Ipsum is simply dummy text of the printing and typesetting industry. Lorem Ipsum has been the industry's standard.</p>
    <div class="read-more">READ MORE <svg width="14" height="12" viewBox="0 0 14 12" fill="none" stroke="var(--teal)" stroke-width="2"><path d="M1 1l5 5-5 5M7 1l5 5-5 5"/></svg></div>
  </article>

  <article class="abs post" style="left:438px">
    <div class="photo" role="img" aria-label="Photo of a foundation construction site with workers" style="background:linear-gradient(180deg,#8fb0d0 0%,#7d9e6a 30%,#9b8f7e 60%,#8a8276 100%)"></div>
    <div class="post-meta">
      <span><svg width="16" height="16" viewBox="0 0 16 16"><rect x="1" y="3" width="14" height="12" fill="none" stroke="var(--teal)" stroke-width="1.8"/><rect x="1" y="3" width="14" height="4" fill="var(--teal)"/><path d="M4 1v3M12 1v3" stroke="var(--teal)" stroke-width="1.8"/></svg>05 May 2017</span>
      <span><svg width="16" height="16" viewBox="0 0 16 16"><path d="M2 14l1-4 8-8 3 3-8 8z" fill="var(--teal)"/></svg>By Admin</span>
    </div>
    <h3 class="post-title">Lorem Ipsum is simply dummy text of the printing.</h3>
    <p class="post-text">Lorem Ipsum is simply dummy text of the printing and typesetting industry. Lorem Ipsum has been the industry's standard.</p>
    <div class="read-more">READ MORE <svg width="14" height="12" viewBox="0 0 14 12" fill="none" stroke="var(--teal)" stroke-width="2"><path d="M1 1l5 5-5 5M7 1l5 5-5 5"/></svg></div>
  </article>

  <article class="abs post" style="left:798px">
    <div class="photo" role="img" aria-label="Photo of a team in hard hats discussing plans" style="background:linear-gradient(135deg,#e4e6e8 0%,#8a96a6 35%,#3f5f9a 60%,#2b2e36 100%)"></div>
    <div class="post-meta">
      <span><svg width="16" height="16" viewBox="0 0 16 16"><rect x="1" y="3" width="14" height="12" fill="none" stroke="var(--teal)" stroke-width="1.8"/><rect x="1" y="3" width="14" height="4" fill="var(--teal)"/><path d="M4 1v3M12 1v3" stroke="var(--teal)" stroke-width="1.8"/></svg>05 May 2017</span>
      <span><svg width="16" height="16" viewBox="0 0 16 16"><path d="M2 14l1-4 8-8 3 3-8 8z" fill="var(--teal)"/></svg>By Admin</span>
    </div>
    <h3 class="post-title">Lorem Ipsum is simply dummy text of the printing.</h3>
    <p class="post-text">Lorem Ipsum is simply dummy text of the printing and typesetting industry. Lorem Ipsum has been the industry's standard.</p>
    <div class="read-more">READ MORE <svg width="14" height="12" viewBox="0 0 14 12" fill="none" stroke="var(--teal)" stroke-width="2"><path d="M1 1l5 5-5 5M7 1l5 5-5 5"/></svg></div>
  </article>
</section>

<section class="contact">
  <h2 class="abs heading">GET IN TOUCH</h2>
  <div class="abs info-card" style="left:78px">
    <svg width="28" height="28" viewBox="0 0 24 24"><path d="M6.6 10.8a15 15 0 0 0 6.6 6.6l2.2-2.2c.3-.3.7-.4 1-.2 1.1.4 2.3.6 3.6.6.6 0 1 .4 1 1V20c0 .6-.4 1-1 1A17 17 0 0 1 3 4c0-.6.4-1 1-1h3.5c.6 0 1 .4 1 1 0 1.3.2 2.5.6 3.6.1.3 0 .7-.2 1z" fill="var(--teal)"/></svg>
    <div>123 456 7890</div>
  </div>
  <div class="abs info-card" style="left:438px">
    <svg width="24" height="30" viewBox="0 0 20 24"><path d="M10 1a8 8 0 0 0-8 8c0 6 8 14 8 14s8-8 8-14a8 8 0 0 0-8-8z" fill="var(--teal)"/><circle cx="10" cy="9" r="3" fill="#fff"/></svg>
    <div>Lorem Ipsum is simply dummy text of<br>the printing and typesetting.</div>
  </div>
  <div class="abs info-card" style="left:798px">
    <svg width="30" height="22" viewBox="0 0 30 22" fill="none" stroke="var(--teal)" stroke-width="2.5"><rect x="1.5" y="1.5" width="27" height="19"/><path d="M2 2l13 10L28 2"/></svg>
    <div>info@keltoconstruction.example.com</div>
  </div>

  <div class="abs field" style="left:78px;top:355px;width:324px">Your Name</div>
  <div class="abs field" style="left:438px;top:355px;width:324px">Your Email</div>
  <div class="abs field" style="left:798px;top:355px;width:324px">Your phone no.</div>
  <div class="abs field" style="left:78px;top:438px;width:1044px">Your Message</div>
  <div class="btn" style="left:527px;top:527px;width:145px;height:42px;font-size:18px">SEND</div>
</section>

<footer class="site-footer">
  <nav class="abs footer-links">
    <a href="#">Home</a><a href="#">About</a><a href="#">Project</a><a href="#">Blog</a><a href="#">Contact</a>
  </nav>
  <p class="abs copyright">©KELTO CONSTRUCTIONS- 2018. All Rights Reserved.</p>
</footer>

</body>
</html>
```